The BRV Relational Philanthropy Cycle

The title for this graphic is above. It must be included.
I am looking for a graphic representation of the relationship between the Christian school and the donor / pointing to the child (student) - the school's mission / outcome of investment through a gift / appreciation of the gift / communication of the gift impact for the child / stronger relationship going back to the child. This is not easy to do. I've tried to do it on my own and can't get it.
Any cliched child representations will be dismissed out of hand e.g. mortar boards, pencils, uniforms etc. The child should be abstract so that gender and race are irrelevant.
The key to this whole thing is the idea of RELATIONSHIP. The close relationship of donor and the Christian school, the pointing of that relationship to focus on the child / the school's mission, the outpouring of generosity that then happens in the heart of the donor and the gift that results, followed up by intentional work by the Christian school to thank and inform the donor - thank for the gift inform about the gift's expenditure and impact in the life of the child - all of which leads to a strengthening of the relationship and continued philanthropy as a never ending cycle.
It must be branded - logo and colors attached.
It must be obvious - easy to grasp the basic idea of relationship resulting in generosity / philanthropy. The visual should be clear - any words used illustrate - I should not 'need' the words to understand the idea.
I need it on a PP slide, jpeg, thumbnail. It must be highly legible in no more than 1/3 of a regular size piece of paper.
Our website is faithacademyworks.example
google donor cultivation cycle or donor giving cycle to see many examples of cycles that are used in secular contexts - the big difference in BRV's is the focus on the child and the importance of the relationship.

```html
<!DOCTYPE html>
<html lang="en">
<head>
<meta charset="utf-8">
<title>The BRV Relational Philanthropy Cycle</title>
<link href="https://fonts.googleapis.com/css2?family=Libre+Baskerville&family=Montserrat:wght@400;500;700&display=swap" rel="stylesheet">
<style>
  :root {
    --page: #f4f4f4;
    --panel: #ffffff;
    --brand-blue: #3f73aa;
    --brand-grey: #7b7b7b;
    --neutral-ring: #d9d9d9;
    --neutral-arc: #8d8d8d;
    --soft-blue: #86a8cf;
    --warm-orange: #eca346;
    --fresh-green: #6aad48;
    --ink: #333333;
  }
  html, body {
    margin: 0;
    padding: 0;
    width: 1200px;
    height: 2307px;
    overflow: hidden;
    background: var(--page);
  }
  .artboard { display: block; width: 1200px; height: 2307px; }
  .panel { fill: var(--panel); }
  .title { font-family: "Libre Baskerville", Georgia, serif; font-size: 23px; fill: var(--brand-grey); }
  .title .brand { fill: var(--brand-blue); }
  .arc-label { font-family: "Montserrat", Arial, sans-serif; font-size: 14px; font-weight: 500; letter-spacing: 0.3px; fill: var(--arc-text); }
  .verse { font-family: "Montserrat", Arial, sans-serif; font-size: 14px; font-weight: 500; fill: var(--verse); }
  .node-label { font-family: "Montserrat", Arial, sans-serif; font-size: 13px; font-weight: 700; fill: #ffffff; }
  .icon-white { fill: none; stroke: #ffffff; stroke-width: 1.4; stroke-linecap: round; stroke-linejoin: round; }
  .legend-title { font-family: "Montserrat", Arial, sans-serif; font-size: 13px; font-weight: 500; fill: #222; }
  .legend-icon { fill: none; stroke: var(--brand-blue); stroke-width: 1.4; stroke-linejoin: round; stroke-linecap: round; }
  .copyright { font-family: "Montserrat", Arial, sans-serif; font-size: 12px; fill: var(--ink); }
  .wordmark { font-family: "Libre Baskerville", Georgia, serif; font-size: 30px; fill: var(--brand-blue); }
</style>
</head>
<body>
<svg class="artboard" viewBox="0 0 850 1634" xmlns="http://www.w3.org/2000/svg" xmlns:xlink="http://www.w3.org/1999/xlink">
  <defs>
    <path id="top-label-path" d="M -161.6 -58.8 A 172 172 0 0 1 161.6 -58.8"/>
    <path id="bottom-label-path" d="M -167.3 60.9 A 178 178 0 0 0 167.3 60.9"/>

    <g id="relational-cycle">
      <!-- cycle arrows -->
      <path d="M -135 -69 A 152 152 0 0 1 113 -101.7" fill="none" stroke="var(--arc)" stroke-width="14"/>
      <polygon points="123.4,-111 102.6,-92.3 129,-83.9" fill="var(--arc)" transform="scale(1.15) translate(-15,13)"/>
      <path d="M 131.6 76 A 152 152 0 0 1 -116.4 97.7" fill="none" stroke="var(--arc)" stroke-width="14"/>
      <polygon points="-104,87 -129,108 -133,77" fill="var(--arc)"/>

      <text class="arc-label"><textPath href="#top-label-path" startOffset="50%" text-anchor="middle">Outpouring of Generosity</textPath></text>
      <text class="arc-label"><textPath href="#bottom-label-path" startOffset="50%" text-anchor="middle">Mission Impact on the Child</textPath></text>

      <!-- relationship ring -->
      <circle r="106" fill="var(--ring)" stroke="var(--ring-line)" stroke-width="1"/>
      <text class="verse" x="0" y="-76" text-anchor="middle">Luke 8:3</text>
      <text class="verse" x="0" y="88" text-anchor="middle">Mark 9:37</text>
      <g fill="var(--brand-blue)">
        <polygon points="-72,-54 -64,-56 -68,-49"/>
        <polygon points="-66,-60 -58,-62 -62,-55"/>
        <polygon points="72,-50 64,-52 68,-45" transform="rotate(90 68 -50)"/>
        <polygon points="66,-56 58,-58 62,-51" transform="rotate(90 62 -56)"/>
        <polygon points="-72,54 -64,56 -68,49"/>
        <polygon points="-66,60 -58,62 -62,55"/>
        <polygon points="72,54 64,56 68,49" transform="rotate(90 68 54)"/>
        <polygon points="66,48 58,50 62,43" transform="rotate(90 62 48)"/>
      </g>

      <!-- nodes -->
      <circle cx="-132" cy="0" r="65" fill="var(--donor)"/>
      <circle cx="132" cy="0" r="65" fill="var(--steward)" stroke="var(--node-line)" stroke-width="1"/>
      <circle cx="0" cy="0" r="var(--child-r)" fill="var(--child)" stroke="var(--node-line)" stroke-width="1"/>
      <line x1="-112" y1="2" x2="112" y2="2" stroke="#ffffff" stroke-width="1"/>

      <!-- donor icon: open hand with heart -->
      <g class="icon-white" transform="translate(-132,-18)">
        <path d="M0 -4 L-7 -11 A4 4 0 0 1 0 -17 A4 4 0 0 1 7 -11 Z"/>
        <path d="M-16 2 h5 l7 3 h8 a2 2 0 0 1 0 4 h-7"/>
        <path d="M-11 13 h9 l14 -7 a2 2 0 0 0 -2 -4 l-8 4"/>
        <path d="M-18 0 v15"/>
      </g>
      <!-- child icon: three abstract figures -->
      <g class="icon-white" transform="translate(0,-14)">
        <circle cx="-9" cy="-11" r="3.2"/>
        <circle cx="0" cy="-14" r="3.2"/>
        <circle cx="9" cy="-11" r="3.2"/>
        <rect x="-12.5" y="-5" width="7" height="17" rx="3.5"/>
        <rect x="-3.5" y="-8" width="7" height="20" rx="3.5"/>
        <rect x="5.5" y="-5" width="7" height="17" rx="3.5"/>
      </g>

      <text class="node-label" x="-132" y="27" text-anchor="middle">DONOR</text>
      <text class="node-label" x="0" y="27" text-anchor="middle">THE CHILD</text>
      <text class="node-label" x="132" y="22" text-anchor="middle">DONOR</text>
      <text class="node-label" x="132" y="40" text-anchor="middle">STEWARD</text>
    </g>

    <g id="steward-dove" class="icon-white">
      <path d="M-10 -10 c4 -2 8 0 10 4 l8 -12 c1 8 -2 14 -7 17 l9 1 c-5 5 -12 6 -18 3 l-4 4"/>
      <path d="M-16 8 h5 l7 3 h8 a2 2 0 0 1 0 4 h-7"/>
      <path d="M-11 19 h9 l14 -7 a2 2 0 0 0 -2 -4 l-8 4"/>
    </g>
    <g id="steward-globe" class="icon-white">
      <circle cx="0" cy="-8" r="11"/>
      <ellipse cx="0" cy="-8" rx="5" ry="11"/>
      <line x1="-11" y1="-8" x2="11" y2="-8"/>
      <line x1="0" y1="-19" x2="0" y2="3"/>
      <path d="M-16 8 h5 l7 3 h8 a2 2 0 0 1 0 4 h-7"/>
      <path d="M-11 19 h9 l14 -7 a2 2 0 0 0 -2 -4 l-8 4"/>
    </g>
    <g id="steward-target" class="icon-white">
      <circle cx="0" cy="-4" r="15"/>
      <circle cx="0" cy="-4" r="10"/>
      <circle cx="0" cy="-4" r="5"/>
      <path d="M0 -4 L13 -17 M10 -17 h3 v-3 M13 -17 l4 -1 M13 -17 l-1 4"/>
    </g>

    <g id="icon-legend">
      <text class="legend-title" x="0" y="0" text-anchor="middle">Icons</text>
      <g class="legend-icon">
        <path d="M-14 58 L-4 40 L2 50 L6 44 L14 58 Z"/>
        <path d="M-4 40 v-12 l9 3 l-9 3"/>
        <path d="M-9 70 h18 v10 c0 7 -9 12 -9 12 c0 0 -9 -5 -9 -12 Z"/>
        <line x1="0" y1="70" x2="0" y2="92"/>
        <line x1="-9" y1="79" x2="9" y2="79"/>
        <polygon points="0,108 3.5,116 12,116 5,121 8,130 0,125 -8,130 -5,121 -12,116 -3.5,116"/>
        <circle cx="0" cy="163" r="12"/>
        <circle cx="0" cy="163" r="7"/>
        <circle cx="0" cy="163" r="2.5"/>
        <path d="M0 163 L11 152 M9 150 l4 0 l0 4"/>
      </g>
    </g>
  </defs>

  <!-- first board -->
  <rect class="panel" x="30" y="24" width="790" height="573"/>
  <text class="title" x="425" y="103" text-anchor="middle"><tspan class="brand">The BRV</tspan> Relational Philanthropy Cycle</text>
  <use href="#relational-cycle" transform="translate(425,328)"
       style="--arc: var(--neutral-arc); --arc-text: var(--brand-blue); --ring: var(--neutral-ring); --ring-line: none; --verse: #111; --donor: var(--brand-blue); --child: var(--brand-blue); --steward: var(--brand-blue); --node-line: none; --child-r: 65px;"/>
  <use href="#steward-dove" transform="translate(557,310)"/>
  <use href="#icon-legend" transform="translate(733,266)"/>
  <text class="copyright" x="90" y="570">© Bright River Ventures 2022</text>
  <text class="wordmark" x="728" y="556" text-anchor="middle">BRV</text>

  <!-- second board -->
  <rect class="panel" x="30" y="627" width="790" height="978"/>
  <text class="title" x="425" y="706" text-anchor="middle"><tspan class="brand">The BRV</tspan> Relational Philanthropy Cycle</text>
  <use href="#relational-cycle" transform="translate(425,931)"
       style="--arc: var(--brand-blue); --arc-text: var(--brand-grey); --ring: var(--soft-blue); --ring-line: none; --verse: #ffffff; --donor: var(--warm-orange); --child: var(--brand-blue); --steward: var(--fresh-green); --node-line: none; --child-r: 71px;"/>
  <use href="#steward-globe" transform="translate(557,919)"/>
  <use href="#icon-legend" transform="translate(733,870)"/>

  <use href="#relational-cycle" transform="translate(425,1335)"
       style="--arc: var(--brand-blue); --arc-text: var(--brand-grey); --ring: var(--soft-blue); --ring-line: #2f5f92; --verse: #ffffff; --donor: var(--warm-orange); --child: var(--brand-blue); --steward: var(--fresh-green); --node-line: #2f5f92; --child-r: 71px;"/>
  <use href="#steward-target" transform="translate(557,1322)"/>

  <text class="copyright" x="90" y="1582">© Bright River Ventures 2022</text>
  <text class="wordmark" x="728" y="1566" text-anchor="middle">BRV</text>
</svg>
</body>
</html>
```